Billboard design 8x3M RAVU (Spanish company)

We´re located in the south of Spain. We run a local telecom company.
We sell Fiber optic, and mobile phone lines mainly.
The billboard will have to be in Spanish, I would like the price to be something you spot on first sight when passing by in the car.
Our company color is blue, like in our logo which I will add. I will also add a example from what we currently have.
The new offer should be:
1000 megas + 100Gigas movil con llamadas ilimitadas. (meaning 1000Mb fiber optic speed and 100Gb data and unlimited calls for 1 mobile line)
Our details are: phone line 958 47 6620
Website: ra-vu.es

```html
<!DOCTYPE html>
<html lang="es">
<head>
<meta charset="utf-8">
<title>RAVU – Valla 8x3</title>
<link href="https://fonts.googleapis.com/css2?family=Saira+Semi+Condensed:wght@500;600;700;800&display=swap" rel="stylesheet">
<style>
  :root {
    --navy: #005a8c;
    --navy-deep: #004f7d;
    --sky: #00c2f2;
    --paper: #ffffff;
    --backdrop: #e9eef3;
  }
  * { margin: 0; padding: 0; box-sizing: border-box; }
  html, body {
    width: 1200px; height: 800px; overflow: hidden;
    background: var(--backdrop);
  }
  .billboard {
    position: absolute; left: 20px; top: 182px;
    width: 1160px; height: 436px;
    display: block;
  }
  .billboard text { font-family: "Saira Semi Condensed", sans-serif; }
  .surface { fill: var(--paper); }
  .price { font-size: 190px; font-weight: 800; fill: var(--navy); }
  .price-lead { font-size: 54px; font-weight: 700; fill: var(--navy-deep); }
  .offer-main { font-size: 78px; font-weight: 700; fill: var(--navy-deep); }
  .offer-sub { font-size: 58px; font-weight: 700; fill: var(--sky); }
  .brand-dot { fill: var(--navy); }
  .brand-name { font-size: 110px; font-weight: 800; fill: var(--sky); }
  .brand-services { font-size: 36px; font-weight: 600; fill: var(--sky); }
  .brand-services .strong { fill: var(--navy-deep); }
  .band-light { fill: var(--sky); }
  .band-dark { fill: var(--navy-deep); }
  .contact-icon-bg { fill: var(--sky); }
  .contact-icon { fill: var(--paper); }
  .contact-text { font-size: 54px; font-weight: 600; fill: var(--paper); }
</style>
</head>
<body>
  <svg class="billboard" viewBox="0 0 1160 436" role="img" aria-label="Valla RAVU: 35€ por sólo, 1000 megas + 100 gigas, móvil con llamadas ilimitadas">
    <rect class="surface" x="0" y="0" width="1160" height="436"/>

    <path class="band-light" d="M0,342 L548,342 C600,340 624,362 648,386 C672,408 700,394 740,394 L1160,394 V436 H0 Z"/>
    <path class="band-dark" d="M0,352 L540,352 C590,350 612,372 636,396 C662,420 700,406 740,406 L1160,406 V436 H0 Z"/>

    <text class="price" x="28" y="205" textLength="296" lengthAdjust="spacingAndGlyphs">35€</text>
    <text class="price-lead" x="62" y="264" textLength="176" lengthAdjust="spacingAndGlyphs">Por sólo</text>

    <text class="offer-main" x="352" y="108" textLength="772" lengthAdjust="spacingAndGlyphs">1000 MEGAS + 100GIGAS</text>
    <text class="offer-sub" x="352" y="180" textLength="772" lengthAdjust="spacingAndGlyphs">MOVIL CON LLAMADAS ILIMITADAS</text>

    <circle class="brand-dot" cx="820" cy="292" r="30"/>
    <text class="brand-name" x="866" y="330" textLength="236" lengthAdjust="spacingAndGlyphs">RAVU</text>
    <text class="brand-services" x="780" y="382" textLength="322" lengthAdjust="spacingAndGlyphs">Wifi | Fibra | <tspan class="strong">Movil | Tv</tspan></text>

    <circle class="contact-icon-bg" cx="56" cy="398" r="27"/>
    <path class="contact-icon" transform="translate(29 371) scale(0.87)" d="M22 16c2-1 4 0 5 2l2 5c1 2 0 3-1 4l-2 2c1 4 5 8 9 9l2-2c1-1 3-2 4-1l5 2c2 1 3 3 2 5l-1 3c-1 2-3 3-5 3-12-1-22-11-23-23 0-2 1-4 3-5z"/>
    <text class="contact-text" x="96" y="417" textLength="440" lengthAdjust="spacingAndGlyphs">958 47 6620 | ra-vu.es</text>
  </svg>
</body>
</html>
```